Business Card Design for Marketing Firm

Looking for business card design for higher end marketing firm. Clean but impressionable/trendy. We are a marketing firm that represents manufacturers in the foodservice equipment and supply industry. Our customers are end users such has hotels, restaurants, country clubs, convention centers and casinos as well as distributors of restaurants supplies and equipment, and manufacturers of foodservice equipment and supplies.
Target Market(s)
Hotels, Restaurants, Supply & Equipment Distributors, Foodservice Manufacturers
Industry/Entity Type
Foodservice/Hospitality
Contact Information for Business Card
Name, Title, Contact Number, Email, Website, Social Media, Address
Requirements
Must have
- Clean & Simple but Serious and Impressionable

```html
<!DOCTYPE html>
<html lang="en">
<head>
<meta charset="utf-8">
<title>Crestline Hospitality Reps – Business Card</title>
<link rel="stylesheet" href="https://fonts.googleapis.com/css2?family=Montserrat:wght@400;500;600;700&display=swap">
<style>
  :root {
    --stage: #e9e6e1;
    --card-white: #ffffff;
    --card-grey: #a6a6a6;
    --navy: #2e2b64;
    --ink: #333333;
    --muted: #555555;
    --band-grey: #cfcfcf;
    --silver: #d6d6d6;
  }
  * { margin: 0; padding: 0; box-sizing: border-box; }
  html, body { width: 900px; height: 1200px; overflow: hidden; }
  body {
    position: relative;
    background: var(--stage);
    font-family: "Montserrat", Arial, sans-serif;
  }
  .card {
    position: absolute;
    left: 80px;
    width: 742px;
    height: 440px;
    border-radius: 30px;
    overflow: hidden;
  }
  .card--front { top: 132px; background: var(--card-white); }
  .card--back { top: 638px; background: var(--card-grey); }

  .brand-name {
    position: absolute;
    left: 40px;
    top: 150px;
    color: var(--navy);
    font-weight: 600;
    font-size: 25px;
    letter-spacing: 0.5px;
    line-height: 1.25;
  }

  .person { position: absolute; right: 44px; top: 278px; text-align: right; }
  .person__name { color: var(--navy); font-weight: 700; font-size: 27px; line-height: 1.1; }
  .person__title { color: var(--muted); font-weight: 500; font-size: 15px; margin-top: 6px; letter-spacing: 0.3px; }

  .divider {
    position: absolute; left: 42px; top: 324px;
    width: 506px; height: 1.5px; background: var(--ink);
  }

  .contacts { position: absolute; left: 38px; top: 341px; list-style: none; }
  .contacts__item {
    display: flex; align-items: center; gap: 12px;
    height: 24px; font-size: 16px; color: var(--ink);
  }
  .contacts__item svg { width: 14px; height: 14px; fill: var(--ink); flex: none; }

  .footer-bands { position: absolute; left: 0; top: 0; width: 742px; height: 440px; }
  .address {
    position: absolute; right: 30px; top: 411px;
    white-space: nowrap;
    line-height: 20px;
    color: #ffffff; font-size: 15.5px; letter-spacing: 0.1px;
  }

  .back-brand {
    position: absolute; left: 0; right: 0; top: 178px;
    text-align: center;
    color: var(--silver);
    font-weight: 600; font-size: 40px; letter-spacing: 1px; line-height: 1.25;
  }
</style>
</head>
<body>

<section class="card card--front" aria-label="Business card front">
  <div class="brand-name">CRESTLINE<br>HOSPITALITY REPS</div>

  <div class="person">
    <div class="person__name">Daniel Reyes</div>
    <div class="person__title">CEO &amp; Founder</div>
  </div>

  <div class="divider"></div>

  <ul class="contacts">
    <li class="contacts__item">
      <svg viewBox="0 0 24 24" aria-hidden="true"><path d="M6.6 10.8a15.1 15.1 0 0 0 6.6 6.6l2.2-2.2c.3-.3.7-.4 1-.2 1.1.4 2.3.6 3.6.6.6 0 1 .4 1 1V20c0 .6-.4 1-1 1A17 17 0 0 1 3 4c0-.6.4-1 1-1h3.5c.6 0 1 .4 1 1 0 1.3.2 2.5.6 3.6.1.3 0 .7-.2 1z"/></svg>
      (555) 014-2290
    </li>
    <li class="contacts__item">
      <svg viewBox="0 0 24 24" aria-hidden="true"><rect x="2" y="5" width="20" height="14"/><path d="M2.5 5.5l9.5 7.5 9.5-7.5" fill="none" stroke="#fff" stroke-width="1.6"/></svg>
      info@crestlinereps.com
    </li>
    <li class="contacts__item">
      <svg viewBox="0 0 24 24" aria-hidden="true"><circle cx="12" cy="12" r="10"/></svg>
      www.crestlinereps.com
    </li>
  </ul>

  <svg class="footer-bands" viewBox="0 0 742 440" aria-hidden="true">
    <polygon points="0,421 312,421 300,440 0,440" fill="var(--band-grey)"/>
    <polygon points="318,440 350,401 742,401 742,440" fill="var(--navy)"/>
  </svg>
  <div class="address">420 Harbor Lane, Suite 300, Bayview, CA 90000</div>
</section>

<section class="card card--back" aria-label="Business card back">
  <div class="back-brand">CRESTLINE<br>HOSPITALITY REPS</div>
</section>

</body>
</html>
```